Veldmark Supplies Business Card

Professional business card that stand out to our potential customers. Front and back with clean modern design

Industry/Entity Type

Oil and gas

Contact Information for Business Card

Name, address, website , office phone and cell number

Requirements
Must have
• Editable files for each employee

```html
<!DOCTYPE html>
<html lang="en">
<head>
<meta charset="utf-8">
<title>Veldmark Supplies — Business Card</title>
<link href="https://fonts.googleapis.com/css2?family=Open+Sans:wght@400;600;700;800&display=swap" rel="stylesheet">
<style>
  :root {
    --bg-dark: #0b0b0b;
    --bg-mid: #3a3a3a;
    --card-black: #141414;
    --card-black-edge: #1f1f1f;
    --emboss: #6c6c6c;
    --paper: #ffffff;
    --brand-red: #ec1b24;
    --brand-blue: #1ea6c9;
    --ink: #2a2a2a;
  }
  * { box-sizing: border-box; margin: 0; padding: 0; }
  html, body { width: 1200px; height: 801px; overflow: hidden; }
  body {
    font-family: "Open Sans", Arial, sans-serif;
    background: radial-gradient(ellipse at 55% 45%, var(--bg-mid) 0%, var(--bg-dark) 75%);
    position: relative;
  }
  .card {
    position: absolute;
    top: 250px;
    width: 520px;
    height: 300px;
    border-radius: 18px;
    overflow: hidden;
    box-shadow: 0 20px 40px rgba(0,0,0,.6);
  }
  /* Back side */
  .card-back {
    left: 60px;
    background: linear-gradient(150deg, var(--card-black-edge), var(--card-black));
    display: flex;
    flex-direction: column;
    align-items: center;
    justify-content: center;
    gap: 18px;
  }
  .card-back .brand-mark {
    width: 54px; height: 54px;
    border: 3px solid var(--emboss);
    border-radius: 8px;
  }
  .card-back .brand-name {
    font-weight: 800;
    font-size: 28px;
    letter-spacing: 1px;
    text-transform: uppercase;
    color: var(--emboss);
  }
  /* Front side */
  .card-front {
    left: 620px;
    background: var(--paper);
  }
  .front-brand {
    position: absolute;
    top: 34px; right: 34px;
    display: flex; align-items: center; gap: 10px;
  }
  .front-brand .brand-mark {
    width: 30px; height: 30px;
    background: var(--brand-red);
    border-radius: 4px;
  }
  .front-brand .brand-name {
    font-weight: 800;
    font-size: 19px;
    text-transform: uppercase;
    color: var(--brand-red);
  }
  .divider {
    position: absolute;
    height: 1px;
    background: var(--brand-red);
  }
  .divider-top { top: 88px; left: 230px; right: 34px; }
  .divider-mid { top: 176px; left: 34px; width: 200px; }
  .person {
    position: absolute;
    top: 118px; left: 34px;
  }
  .person-name {
    font-weight: 800;
    font-size: 26px;
    line-height: 1;
    color: var(--brand-red);
    text-transform: uppercase;
  }
  .person-title {
    font-size: 14px;
    color: var(--brand-blue);
    margin-top: 6px;
  }
  .contact-list {
    position: absolute;
    top: 188px; left: 34px;
    list-style: none;
    font-size: 12.5px;
    color: var(--ink);
    line-height: 1.6;
  }
  .contact-list li { display: flex; align-items: center; gap: 8px; }
  .contact-list svg { width: 11px; height: 11px; fill: var(--brand-blue); flex: none; }
  .company-block {
    position: absolute;
    top: 104px; right: 34px;
    text-align: right;
    font-size: 12.5px;
    color: var(--ink);
    line-height: 1.55;
  }
  .company-block .company-name {
    font-weight: 600;
    color: var(--brand-blue);
    font-size: 13.5px;
  }
  .footer-band {
    position: absolute;
    left: 0; right: 0; bottom: 0;
    height: 12px;
    display: flex;
  }
  .footer-band .band-red { flex: 1; background: var(--brand-red); }
  .footer-band .band-blue { width: 120px; background: var(--brand-blue); }
</style>
</head>
<body>
  <section class="card card-back" aria-label="Card back">
    <div class="brand-mark"></div>
    <div class="brand-name">Veldmark Supplies</div>
  </section>

  <section class="card card-front" aria-label="Card front">
    <div class="front-brand">
      <div class="brand-mark"></div>
      <div class="brand-name">Veldmark Supplies</div>
    </div>
    <div class="divider divider-top"></div>

    <div class="person">
      <div class="person-name">Daniel Marsh</div>
      <div class="person-title">Founder &amp; CEO</div>
    </div>
    <div class="divider divider-mid"></div>

    <ul class="contact-list">
      <li><svg viewBox="0 0 24 24"><path d="M6.6 10.8a15 15 0 0 0 6.6 6.6l2.2-2.2a1 1 0 0 1 1-.25 11.4 11.4 0 0 0 3.6.57 1 1 0 0 1 1 1V20a1 1 0 0 1-1 1A17 17 0 0 1 3 4a1 1 0 0 1 1-1h3.5a1 1 0 0 1 1 1c0 1.25.2 2.45.57 3.57a1 1 0 0 1-.25 1z"/></svg>(123) 456-7890</li>
      <li><svg viewBox="0 0 24 24"><path d="M7 1h10a2 2 0 0 1 2 2v18a2 2 0 0 1-2 2H7a2 2 0 0 1-2-2V3a2 2 0 0 1 2-2zm0 3v14h10V4z"/></svg>(123) 456-7890</li>
      <li><svg viewBox="0 0 24 24"><path d="M6 2h12v6H6zM4 9h16a2 2 0 0 1 2 2v6h-4v5H6v-5H2v-6a2 2 0 0 1 2-2zm4 7v4h8v-4z"/></svg>(123) 456-7890</li>
      <li><svg viewBox="0 0 24 24"><path d="M2 5h20v14H2zm2 2v.5l8 5 8-5V7z"/></svg>info@yourwebsitehere.com</li>
    </ul>

    <div class="company-block">
      <div class="company-name">Veldmark Supplies</div>
      <div>423 Street Address Here, City</div>
      <div>State &amp; Country, ZIP Code</div>
      <div>www.yourwebsitehere.com</div>
    </div>

    <div class="footer-band"><div class="band-red"></div><div class="band-blue"></div></div>
  </section>
</body>
</html>
```